Private Investment Firm Needs PowerPoint Presentation Template

Design PowerPoint template, take Pinebrook-submitted rough presentation draft, and drop it into new template. See attached Project Brief file for more detail.
Updates

Some decent designs have been submitted but they seem to lack the understanding of our target markets. I am hopeful that more time and feedback will result in better results.

Target Market(s)

Private company owners and intermediaries.

Font styles to use
Serif

Colors
3176b5

Requirements
Must have
• See attached Project Brief.
Nice to have
Should not have
• No B2C fluff--this is a B2B project.

```html
<!DOCTYPE html>
<html lang="en">
<head>
<meta charset="utf-8">
<title>When Is a Non-Control Transaction Appropriate?</title>
<link href="https://fonts.googleapis.com/css2?family=Montserrat:wght@400;500;600;700&family=Libre+Baskerville&display=swap" rel="stylesheet">
<style>
  :root {
    --brand-blue: #1a6fc4;
    --bar-blue: #0b6dc0;
    --ink: #1f1f1f;
    --paper: #ffffff;
    --photo-deep: #0d3f7a;
    --photo-mid: #3f86c6;
    --photo-light: #a9cdea;
  }
  * { margin: 0; padding: 0; box-sizing: border-box; }
  html, body { width: 1200px; height: 676px; overflow: hidden; background: var(--paper); }
  .slide {
    position: relative;
    width: 1200px;
    height: 676px;
    overflow: hidden;
    background: var(--paper);
    font-family: "Montserrat", Arial, sans-serif;
    color: var(--ink);
  }
  .side-bar {
    position: absolute;
    left: 0; top: 0;
    width: 44px; height: 676px;
    background: var(--bar-blue);
  }
  .side-bar__url {
    position: absolute;
    left: 22px; top: 337px;
    transform: translate(-50%, -50%) rotate(-90deg);
    white-space: nowrap;
    font-family: "Libre Baskerville", Georgia, serif;
    font-size: 14px;
    color: var(--paper);
    letter-spacing: 0.2px;
  }
  .slide-title {
    position: absolute;
    left: 86px; top: 80px;
    font-weight: 700;
    font-size: 29px;
    line-height: 34px;
    color: var(--brand-blue);
    letter-spacing: 0.3px;
  }
  .criteria {
    position: absolute;
    left: 86px; top: 176px;
    width: 520px;
    list-style: none;
    font-size: 17px;
    line-height: 28px;
    letter-spacing: 0.2px;
  }
  .criteria li {
    position: relative;
    padding-left: 28px;
  }
  .criteria li::before {
    content: "";
    position: absolute;
    left: 4px; top: 9px;
    width: 9px; height: 9px;
    border: 3px solid var(--brand-blue);
    transform: rotate(45deg);
  }
  .criteria .sub { list-style: none; }
  .criteria .sub li { padding-left: 23px; }
  .criteria .sub li::before { left: 0; }
  .emphasis {
    font-weight: 700;
    text-decoration: underline;
    text-underline-offset: 3px;
  }
  .brand {
    position: absolute;
    left: 68px; top: 614px;
    display: flex;
    align-items: center;
    gap: 10px;
    font-family: "Montserrat", Arial, sans-serif;
    font-weight: 600;
    font-size: 18px;
    color: var(--brand-blue);
    letter-spacing: 1px;
  }
  .brand__dot {
    width: 34px; height: 34px;
    border-radius: 50%;
    background: var(--brand-blue);
  }
  .hero-image {
    position: absolute;
    left: 645px; top: 0;
    width: 555px; height: 676px;
    background: linear-gradient(180deg, var(--photo-mid) 0%, var(--photo-light) 40%, var(--photo-mid) 70%, var(--photo-deep) 100%);
  }
  .page-number {
    position: absolute;
    right: 32px; top: 18px;
    font-family: "Libre Baskerville", Georgia, serif;
    font-size: 16px;
    color: var(--ink);
  }
</style>
</head>
<body>
<div class="slide">
  <div class="side-bar"><span class="side-bar__url">www.pinebrookcapital.com</span></div>

  <h1 class="slide-title">WHEN IS A NON-CONTROL<br>TRANSACTION APPROPRIATE?</h1>

  <ul class="criteria">
    <li>The company has opportunities to expand but requires capital to do so</li>
    <li>At least one active owner <span class="emphasis">is not</span> close to retirement</li>
    <li>The company is not in a turnaround situation</li>
    <li>Family members may work in the business and want to continue</li>
    <li>Owners care about keeping the business in their family name (legacy)</li>
    <li>Liquidity (dividend) is not the major use of the invested capital</li>
    <li>Owners are sensitive to utilizing too much debt</li>
    <li>Companies require more than just capital:
      <ul class="sub">
        <li>They may also need operational, marketing, financial, and/or technology counsel</li>
      </ul>
    </li>
  </ul>

  <div class="brand"><span class="brand__dot"></span><span>PINEBROOK CAPITAL</span></div>

  <div class="hero-image" role="img" aria-label="Photo of four cheering businesspeople in suits over a world map with glowing network lines and stock figures"></div>
  <div class="page-number">3</div>
</div>
</body>
</html>
```